QHX Compliant Dietary Supplement Label for Nutritional Company

We are in need of a label for our line of 20+ dietary supplements that are specifically formulated to balance body chemistry and match the biochemical individuality of our users based on hair tissue mineral analysis.

We have a line of approximately 20 different dietary supplements that will require use of new label in both a small (90 capsule) and large (180 capsule) size. We will start with the initial label in which Product name, Supplement Facts, and Ingredient list will need to be modified for each particular product thereafter.

The label will be placed on a transparent blue bottle with the color of lid being decided after label design. We are open to a transparent light amber bottle with black lid but blue is our preference.

We would like the majority of the label to be blue. Solid blue, fading of blue to darker blue/black, or subtle background designs are welcome with involvement of white and hints of orange. We do not want pictorial images on the label.

Label size:
Small bottle (120cc): Label size ~ 2.25” x 5.875”
Large bottle (200cc): Label size ~ 2.75” x 7.625”

Front:
-Logo near top of label with product name and description in middle and capsule count near the bottom

Right Side:
-Supplement Facts: See current product image below in brief
-Ingredient list: See current product image below in brief
-Manufactured for: See image below (This is on the left side of our current bottle and would like it moved to the bottom of the right side)

Left side:
-Suggested use: See current product image below in brief
-Leave room for possible warning statement
-Leave room for possible lot number printing
-Keep out of the reach of children.

The first files below are our current supplement label with product information. This information is what is needed on the label and will likely need some adjustments as we are updating our line of supplements and changes in QHX requirements.

The following files are the logo files and color palette.

The remaining files are some designs we came across for inspiration.

Thank you.

Target Market(s)

Health Care Profressionals

Industry/Entity Type

Health Care and Nutrition

Requirements
Nice to have
• Product name needs to be on same line in all one color
Should not have
• Pictorial Images

```html
<!DOCTYPE html>
<html lang="en">
<head>
<meta charset="utf-8">
<title>Kelva-Dren Adrenal Supplement Label</title>
<link href="https://fonts.googleapis.com/css2?family=Montserrat:wght@400;500;600;800&family=Lato:wght@400;700;900&display=swap" rel="stylesheet">
<style>
  :root {
    --navy-top: #0e1838;
    --navy-mid: #152457;
    --navy-bottom: #24399a;
    --orange: #f07a22;
    --brand-blue: #4a78c9;
    --white: #ffffff;
    --ink-blue: #1f3590;
    --canvas: #ffffff;
  }
  * { box-sizing: border-box; margin: 0; padding: 0; }
  html, body {
    width: 1200px; height: 906px; overflow: hidden;
    background: var(--canvas);
    font-family: "Montserrat", sans-serif;
  }
  .label {
    position: absolute; left: 40px; top: 238px;
    width: 1120px; height: 428px;
    background: linear-gradient(180deg, var(--navy-top) 0%, var(--navy-mid) 45%, var(--navy-bottom) 100%);
    color: var(--white);
    box-shadow: 0 3px 6px rgba(0,0,0,0.25);
    overflow: hidden;
  }
  .label__rule-top {
    position: absolute; left: 0; right: 0; top: 9px; height: 2px; background: var(--orange);
  }
  .label__band-bottom {
    position: absolute; left: 0; right: 0; bottom: 0; height: 9px; background: var(--orange);
  }

  /* Left panel */
  .usage {
    position: absolute; left: 32px; top: 34px; width: 276px;
    font-size: 15px; line-height: 19px; font-weight: 400;
    padding-bottom: 13px; border-bottom: 2px solid var(--white);
  }
  .notice {
    position: absolute; left: 32px; top: 257px; width: 276px; height: 71px;
    background: var(--white); border: 2px solid var(--orange); border-radius: 6px;
    color: var(--ink-blue); font-size: 15px; line-height: 19px; padding: 5px 12px;
  }
  .notice strong { font-weight: 800; }
  .batch {
    position: absolute; left: 32px; width: 276px; font-size: 15px;
    display: flex; align-items: flex-end; gap: 4px;
  }
  .batch--lot { top: 347px; }
  .batch--exp { top: 374px; }
  .batch__line { flex: 1; border-bottom: 1px solid var(--white); height: 14px; }

  /* Front panel */
  .brand {
    position: absolute; left: 459px; top: 60px; width: 200px;
    text-align: center; color: var(--brand-blue); font-weight: 500;
  }
  .brand__dot {
    display: block; width: 34px; height: 34px; margin: 0 auto 6px;
    border: 4px solid var(--orange); border-radius: 50%;
  }
  .brand__name { font-size: 29px; line-height: 30px; letter-spacing: 1px; display: block; }
  .brand__sub { font-size: 11px; letter-spacing: 4px; display: block; margin-top: 2px; }
  .product {
    position: absolute; left: 359px; width: 400px; text-align: center;
  }
  .product__name { top: 180px; font-size: 57px; font-weight: 800; line-height: 64px; letter-spacing: -0.5px; }
  .product__desc { top: 250px; font-size: 26px; font-weight: 500; color: var(--orange); letter-spacing: 0.5px; }
  .count { position: absolute; left: 390px; top: 342px; line-height: 1; }
  .count__num { font-size: 50px; font-weight: 400; display: block; letter-spacing: -2px; }
  .count__unit { font-size: 11px; display: block; margin-top: 2px; }
  .category {
    position: absolute; right: 392px; top: 371px; text-align: right;
    font-size: 16px; font-weight: 500; line-height: 19px;
  }

  /* Right panel */
  .facts {
    position: absolute; left: 814px; top: 38px; width: 272px; height: 296px;
    border: 1.5px solid var(--white); border-radius: 4px; padding: 4px 9px;
    font-family: "Lato", sans-serif; font-size: 10px; line-height: 11px;
  }
  .facts__title { font-size: 22px; font-weight: 900; line-height: 26px; }
  .facts__serving { font-weight: 700; font-size: 10px; line-height: 13px; }
  .facts__rule-thick { border-top: 5px solid var(--white); margin: 4px 0 2px; }
  .facts__rule-mid { border-top: 3px solid var(--white); margin: 2px 0; }
  .facts__head, .facts__row {
    display: grid; grid-template-columns: 1fr 50px 44px; align-items: end;
  }
  .facts__head { font-size: 8px; font-weight: 700; line-height: 8px; text-align: right; padding-bottom: 2px; }
  .facts__row { border-top: 1px solid rgba(255,255,255,0.8); padding: 1px 0; }
  .facts__row span:nth-child(2), .facts__row span:nth-child(3) { text-align: right; }
  .facts__row--glandular { font-size: 9.5px; }
  .facts__note { margin-top: 2px; font-size: 10px; }
  .ingredients, .distributor {
    position: absolute; left: 806px; width: 290px;
    font-family: "Lato", sans-serif; font-size: 10.5px; line-height: 12px;
  }
  .ingredients { top: 343px; }
  .distributor { top: 378px; }
  .highlight { color: var(--orange); font-weight: 700; }
</style>
</head>
<body>
  <section class="label" aria-label="Kelva-Dren supplement label">
    <div class="label__rule-top"></div>

    <p class="usage">SUGGESTED USE: One capsule daily or as directed by a physician.</p>
    <p class="notice"><strong>NOTICE:</strong> It is advisable to keep this and all supplements out of the reach of children.</p>
    <p class="batch batch--lot">LOT #:<span class="batch__line"></span></p>
    <p class="batch batch--exp">EXP:<span class="batch__line"></span></p>

    <div class="brand">
      <span class="brand__dot"></span>
      <span class="brand__name">KELVARA</span>
      <span class="brand__sub">LABORATORIES</span>
    </div>
    <h1 class="product product__name">KELVA-DREN</h1>
    <p class="product product__desc">ADRENAL SUPPLEMENT</p>
    <p class="count"><span class="count__num">90</span><span class="count__unit">CAPSULES</span></p>
    <p class="category">DIETARY<br>SUPPLEMENT</p>

    <div class="facts">
      <h2 class="facts__title">Supplement Facts</h2>
      <p class="facts__serving">Serving Size: 1 Capsule<br>Servings Per Container 90</p>
      <div class="facts__rule-thick"></div>
      <div class="facts__head"><span></span><span>Amount Per Serving</span><span>% Daily Value</span></div>
      <div class="facts__row"><span>Vitamin C (as ascorbic acid)</span><span>100 mg</span><span>111%</span></div>
      <div class="facts__row"><span>Vitamin B5<br>&nbsp;(as D-calcium pantothenate)</span><span>100 mg</span><span>2000%</span></div>
      <div class="facts__row"><span>Magnesium (as magnesium amino<br>&nbsp;acid chelate)</span><span>5 mg</span><span>1%</span></div>
      <div class="facts__row"><span>Zinc (as zinc amino acid chelate)</span><span>1 mg</span><span>9%</span></div>
      <div class="facts__row"><span>Manganese (as manganese<br>&nbsp;amino acid chelate)</span><span>1 mg</span><span>43%</span></div>
      <div class="facts__row"><span>Potassium (as potassium<br>&nbsp;amino acid chelate)</span><span>25 mg</span><span>1%</span></div>
      <div class="facts__rule-mid"></div>
      <div class="facts__row facts__row--glandular"><span>Suprarenal (adrenal) powder (bovine)</span><span>100 mg</span><span>†</span></div>
      <div class="facts__row facts__row--glandular"><span>Liver Powder, defatted (bovine)</span><span>45 mg</span><span>†</span></div>
      <div class="facts__row facts__row--glandular"><span>Betain Hydrochloride</span><span>25 mg</span><span>†</span></div>
      <div class="facts__rule-mid"></div>
      <p class="facts__note">† Daily Value not established</p>
    </div>
    <p class="ingredients"><span class="highlight">Other Ingredients:</span> Hypromellose (Vegetable Capsule), Pura-GLIDE (R) (Organic Rice Fiber)</p>
    <p class="distributor"><span class="highlight">Distributed by:</span> KELVARA LABORATORIES, INC.<br>Mesa Linda, AZ 85099 USA</p>

    <div class="label__band-bottom"></div>
  </section>
</body>
</html>
```